Agrarhandel benötigt Homepage
Zielgruppe
Wir sind ein Agrarhandel mit einem Warenumschlagslager im Sinne eines klassischen Einzelhandels und vertreiben Produkte an Landwirte.
Wir vertreiben folgende Hauptproduktgruppen:
Einzelfuttermittel
wie z.B. Sojaexktraktionsschrot. Die einzelnen Produkte könnten z.B. wie die Futtermittel auf folgender Seite dargestellt werden (https://www.kornprobe-beispiel.eu/de/produkt/trelomixan)
Mischfuttermittel
Hier bieten wir unseren Kunden an, individuelles Mischfutter auf Basis unserer Einzelfuttermittel herzustellen.
Weitere Details und weitere Produktbereiche habe ich in einer Powerpoint-Übersicht dargestellt.
Neben diesen Produkten wollen wir uns als Familienunternehmen selbst vorstellen. Zudem betreiben wir in unserer Familie zusätzlich einen Milchviehbetrieb den wir ebenfalls hervorheben möchten, da wir unseren Kunden gegenüber einerseits als Zulieferer aber auch als Kollege auftreten wollen.
Einzelfuttermittel: Hier können wir durch unsere Unabhängigkeit punkten, da wir nicht abhängig von bestimmten Lieferanten sind und dementsprechend unabhängig beraten können. Wir untersuchen im Vergleich zu unseren Wettbewerben die Qualität der Futtermittel bis ins Detail und können daher eine Transparenz bieten, die Konkurrenten in der Regel nicht bieten können. Unser Warenumschlagsplatz mit moderner Technik ermöglicht es uns äußerst kosteneffizient die Waren umschlagen und ausliefern zu können.
Mischfuttermittel: Auf Basis der vorhandenen Einzelfuttermittel stellen wir je nach Kundenwunsch individuelle Mischfutter her. Wir arbeiten mit offenen Deklarationen, sodass unsere Kunden jederzeit nachvollziehen können, ob auch die Einzelfuttermittel verwendet wurden, die sie bestellt haben und keine billigen Ersatzprodukte verwendet wurden.
Zudem sind wir BT und HUPA zertifiziert. Die aktuellen für unser Unternehmen ausgestellten Zertifikate müssen für unsere Kunden als Download zur Verfügung stehen. Statt dem HUPA-Logo bitte das ..
Aufgabenstellung
Wir möchten gerne ein zeitgemäße Homepage, jedoch muss auch berücksichtigt werden, dass unsere Kunden eher konservativ denken.

```html
<!DOCTYPE html>
<html lang="de">
<head>
<meta charset="utf-8">
<title>Altmühl Agrarhandel</title>
<link href="https://fonts.googleapis.com/css2?family=League+Spartan:wght@400;500;600;700;800&family=Josefin+Sans:wght@400;600&family=Baloo+2:wght@700;800&display=swap" rel="stylesheet">
<style>
:root{
  --green-dark:#146b4f;
  --green:#4e8f6b;
  --orange:#f8ab26;
  --yellow:#f2c31a;
  --ink:#111;
  --white:#fff;
  --red:#e21b2b;
}
*{margin:0;padding:0;box-sizing:border-box}
html,body{width:1200px;height:2987px;overflow:hidden;background:var(--white);font-family:"League Spartan",sans-serif;color:var(--ink)}
.page{position:relative;width:1200px;height:2987px;overflow:hidden}
.abs{position:absolute}
/* header */
.header{left:0;top:0;width:1200px;height:115px;background:var(--green-dark)}
.header-accent{left:0;top:0;width:70px;height:115px;background:var(--orange)}
.brand{left:70px;top:0;width:195px;height:115px;background:var(--white);display:flex;flex-direction:column;align-items:center;justify-content:flex-end;padding-bottom:14px;gap:10px}
.brand-mark{width:46px;height:46px;border-radius:50%;background:var(--orange)}
.brand-name{font-weight:600;font-size:15px;color:var(--green-dark);letter-spacing:.2px}
.nav{left:434px;top:52px;display:flex;gap:19px;font-family:"League Spartan",sans-serif;font-weight:600;font-size:15.5px;color:var(--white);letter-spacing:.4px}
.nav .active{color:var(--orange)}
.search{left:1136px;top:50px}
/* hero */
.hero-photo{left:0;top:115px;width:1200px;height:590px;background:linear-gradient(160deg,#5f7a2a 0%,#c7a227 40%,#e8c640 60%,#7d9a2d 100%)}
.hero-cut{left:0;top:470px}
.hero-kicker{left:290px;top:212px;color:#f3e6b0;font-size:19px;font-weight:400}
.hero-title{left:88px;top:232px;font-family:"Baloo 2",sans-serif;font-weight:800;font-size:41px;color:var(--orange);letter-spacing:.3px}
.hero-sub{left:89px;top:284px;width:560px;font-family:"Baloo 2",sans-serif;font-weight:700;font-size:21px;line-height:23px;color:var(--white)}
.hero-btn{left:89px;top:374px;width:136px;height:32px;border-radius:16px;background:var(--orange)}
.thumb{top:452px;width:198px;height:255px}
/* why */
.why-band{left:0;top:808px}
.why-frame{left:741px;top:745px;width:459px;height:312px;background:var(--orange);border-radius:18px 0 0 0}
.why-photo{left:726px;top:762px;width:459px;height:309px;background:linear-gradient(135deg,#6f9a4d,#8a4f2c 55%,#d8d0c4)}
.why-title{left:292px;top:852px;font-family:"Josefin Sans",sans-serif;font-size:35px;color:var(--white);letter-spacing:.5px}
.why-text{left:288px;top:915px;width:390px;font-family:Arial,sans-serif;font-size:9.5px;line-height:12px;color:var(--white)}
.feat{width:160px;display:flex;gap:10px;font-family:Arial,sans-serif;color:var(--white)}
.feat-dot{flex:none;width:19px;height:19px;border-radius:50%;background:var(--orange);margin-top:2px}
.feat h4{font-size:10px;font-weight:700;margin-bottom:6px}
.feat p{font-size:8.5px;line-height:10.5px;opacity:.9}
.ask-btn{left:527px;top:1127px;width:91px;height:25px;border-radius:13px;background:var(--orange);color:var(--ink);font-family:Arial,sans-serif;font-weight:700;font-size:12.5px;display:flex;align-items:center;justify-content:center}
/* certificates */
.badge-a{left:95px;top:1250px;width:135px;height:135px;border-radius:8px;background:#5db33a;border:2px solid #cfe8c2}
.badge-b{left:408px;top:1250px;width:108px;height:122px;background:#f4f8ff;border:2px solid #2a76c9}
.cert-and{left:297px;top:1293px;font-family:Arial,sans-serif;font-weight:700;font-size:21px}
.cert-label{left:228px;top:1375px;font-family:"Josefin Sans",sans-serif;font-weight:600;font-size:38px}
.dl-btn{left:722px;top:1325px;width:352px;height:86px;border-radius:43px;background:var(--orange);box-shadow:6px 7px 10px rgba(0,0,0,.25);display:flex;flex-direction:column;align-items:center;justify-content:center;font-family:"Baloo 2",sans-serif;font-weight:800;font-size:33px;line-height:32px;color:var(--ink)}
.rule{left:0;width:1200px;height:10px;background:var(--green-dark)}
/* products */
.sec-title{left:66px;top:1625px;font-weight:600;font-size:35px;letter-spacing:.4px}
.card{top:1729px;width:215px;height:274px}
.card-img{width:215px;height:181px}
.card-foot{position:relative;height:93px;background:var(--green)}
.card-name{position:absolute;left:11px;top:16px;font-weight:600;font-size:19px;color:var(--ink)}
.card-buy{position:absolute;left:11px;top:60px;width:90px;height:24px;background:#1b1b1b;color:var(--white);font-weight:700;font-size:15px;display:flex;align-items:center;justify-content:center}
.card-heart{position:absolute;right:9px;top:60px}
/* faq */
.faq-title{left:0;top:2198px;width:1230px;text-align:center;font-family:"Baloo 2",sans-serif;font-weight:800;font-size:37px;color:var(--green-dark);letter-spacing:.5px}
.bubble{top:2338px}
.bubble-text{font-family:Arial,sans-serif;font-size:12.5px;line-height:16px;color:#1a2a20}
.avatar{width:58px;height:58px;border-radius:50%;background:#e9ece9;border:3px solid var(--white);box-shadow:0 0 0 1px #ccc}
.dot{top:2510px;width:62px;height:9px;border-radius:5px;background:var(--yellow)}
/* footer */
.foot-band{left:0;top:2568px;width:1200px;height:50px;background:var(--green-dark)}
.foot-col{top:2665px;font-family:"Josefin Sans",sans-serif;font-size:17.5px;line-height:28.5px;color:var(--green-dark)}
.foot-col .lbl{color:var(--orange)}
.contact-row{display:flex;align-items:center;gap:7px}
.ic{width:14px;height:14px;flex:none}
.mini-a{left:1037px;top:2706px;width:64px;height:64px;border-radius:6px;background:#5db33a;border:2px solid #cfe8c2}
.mini-b{left:1114px;top:2706px;width:55px;height:62px;background:#f4f8ff;border:2px solid #2a76c9}
.terms{left:0;top:2842px;width:1200px;text-align:center;font-family:"Josefin Sans",sans-serif;font-size:17px;line-height:28.5px;color:var(--ink)}
.foot-bottom{left:0;top:2937px;width:1200px;height:50px;background:var(--green-dark);display:flex;align-items:center;justify-content:center;font-family:Arial,sans-serif;font-size:11px;color:#3a2a1a}
</style>
</head>
<body>
<div class="page">

  <header>
    <div class="abs header"></div>
    <div class="abs header-accent"></div>
    <div class="abs brand"><span class="brand-mark"></span><span class="brand-name">ALTMÜHL AGRARHANDEL</span></div>
    <nav class="abs nav">
      <span class="active">LANDWIRT</span><span>GESCHÄFTSPARTNER</span><span>LIEFERANTEN</span><span>PRODUKTE ⌄</span><span>FIRMENPRÄSENTATION</span>
    </nav>
    <svg class="abs search" width="26" height="26" viewBox="0 0 26 26"><circle cx="10" cy="10" r="8" fill="none" stroke="#fff" stroke-width="2.2"/><line x1="16" y1="16" x2="24" y2="24" stroke="#fff" stroke-width="2.5" stroke-linecap="round"/></svg>
  </header>

  <section class="hero">
    <div class="abs hero-photo" role="img" aria-label="Kuh auf sonniger Weide im Abendlicht"></div>
    <svg class="abs hero-cut" width="1200" height="240" viewBox="0 0 1200 240"><polygon points="0,10 1200,210 1200,240 0,240" fill="#fff"/></svg>
    <div class="abs hero-kicker">LOREM IPSUM</div>
    <div class="abs hero-title">CONSECTETUR ADIPISCING ELIT</div>
    <div class="abs hero-sub">Excepteur sint occaecat cupidatat non proident, sunt in culpa qui officia deserunt mollit anim id es</div>
    <div class="abs hero-btn"></div>
    <div class="abs thumb" style="left:178px;border-radius:14px 0 0 14px;background:linear-gradient(135deg,#b98a4a,#e6b65a 50%,#7a5a35)" role="img" aria-label="Sack mit Sojabohnen"></div>
    <div class="abs thumb" style="left:396px;background:linear-gradient(135deg,#6f6150,#9a7a5c 50%,#4a3a2c)" role="img" aria-label="Eimer mit Getreidekörnern"></div>
    <div class="abs thumb" style="left:613px;background:linear-gradient(180deg,#cfe0dc,#c89a55 45%,#9b6a30)" role="img" aria-label="Heuballen auf dem Feld"></div>
    <div class="abs thumb" style="left:831px;border-radius:0 14px 0 0;background:radial-gradient(circle at 50% 55%,#c99a5e,#e8cba2 55%,#fff 75%)" role="img" aria-label="Haufen Weizenkörner"></div>
  </section>

  <section class="why">
    <svg class="abs why-band" width="1200" height="470" viewBox="0 0 1200 470"><polygon points="0,0 1200,0 1200,467 0,310" fill="#4e8f6b"/></svg>
    <div class="abs why-frame"></div>
    <div class="abs why-photo" role="img" aria-label="Kuh auf einer Bergweide"></div>
    <h2 class="abs why-title">Warum Uns Wählen?</h2>
    <p class="abs why-text">Excepteur sint occaecat cupidatat non proident, sunt in culpa qui officia deserunt mollit anim id es</p>
    <div class="abs feat" style="left:288px;top:964px"><span class="feat-dot"></span><div><h4>Lorem Ipsum</h4><p>Excepteur sint occaecat cupidatat non proident, sunt in culpa</p></div></div>
    <div class="abs feat" style="left:472px;top:964px"><span class="feat-dot"></span><div><h4>Lorem Ipsum</h4><p>Excepteur sint occaecat cupidatat non proident, sunt in culpa</p></div></div>
    <div class="abs feat" style="left:288px;top:1041px"><span class="feat-dot"></span><div><h4>Lorem Ipsum</h4><p>Excepteur sint occaecat cupidatat non proident, sunt in culpa</p></div></div>
    <div class="abs feat" style="left:472px;top:1041px"><span class="feat-dot"></span><div><h4>Lorem Ipsum</h4><p>Excepteur sint occaecat cupidatat non proident, sunt in culpa</p></div></div>
    <div class="abs ask-btn">Frag Uns</div>
  </section>

  <section class="certs">
    <div class="abs badge-a" role="img" aria-label="HUPA Prüfsiegel"></div>
    <div class="abs cert-and">und</div>
    <div class="abs badge-b" role="img" aria-label="BT Qualitätssiegel"></div>
    <div class="abs cert-label">zertifiziert</div>
    <div class="abs dl-btn"><span>Herunterladen</span><span>Zertifikat</span></div>
  </section>

  <div class="abs rule" style="top:1518px"></div>

  <section class="products">
    <h2 class="abs sec-title">Am Meisten Nachgefragte Produkte</h2>
    <div class="abs card" style="left:57px"><div class="card-img" style="background:radial-gradient(circle at 50% 50%,#c99a5e,#e6c89c 60%,#fff 78%)" role="img" aria-label="Weizenkörner"></div><div class="card-foot"><span class="card-name">Lorem Ipsum</span><span class="card-buy">Kaufen</span><svg class="card-heart" width="22" height="20" viewBox="0 0 22 20"><path d="M11 19 2 10C-1 6 2 1 6 1c2 0 4 1 5 3 1-2 3-3 5-3 4 0 7 5 4 9z" fill="#e21b2b"/></svg></div></div>
    <div class="abs card" style="left:354px"><div class="card-img" style="background:linear-gradient(135deg,#6f6150,#9a7a5c 50%,#4a3a2c)" role="img" aria-label="Eimer mit Getreide"></div><div class="card-foot"><span class="card-name">Lorem Ipsum</span><span class="card-buy">Kaufen</span><svg class="card-heart" width="22" height="20" viewBox="0 0 22 20"><path d="M11 19 2 10C-1 6 2 1 6 1c2 0 4 1 5 3 1-2 3-3 5-3 4 0 7 5 4 9z" fill="#e21b2b"/></svg></div></div>
    <div class="abs card" style="left:651px"><div class="card-img" style="background:linear-gradient(135deg,#b98a4a,#e6b65a 50%,#7a5a35)" role="img" aria-label="Sojabohnen im Sack"></div><div class="card-foot"><span class="card-name">Lorem Ipsum</span><span class="card-buy">Kaufen</span><svg class="card-heart" width="22" height="20" viewBox="0 0 22 20"><path d="M11 19 2 10C-1 6 2 1 6 1c2 0 4 1 5 3 1-2 3-3 5-3 4 0 7 5 4 9z" fill="#e21b2b"/></svg></div></div>
    <div class="abs card" style="left:949px"><div class="card-img" style="background:linear-gradient(180deg,#cfe0dc,#c89a55 45%,#9b6a30)" role="img" aria-label="Heuballen"></div><div class="card-foot"><span class="card-name">Lorem Ipsum</span><span class="card-buy">Kaufen</span><svg class="card-heart" width="22" height="20" viewBox="0 0 22 20"><path d="M11 19 2 10C-1 6 2 1 6 1c2 0 4 1 5 3 1-2 3-3 5-3 4 0 7 5 4 9z" fill="#e21b2b"/></svg></div></div>
  </section>

  <div class="abs rule" style="top:2115px"></div>

  <section class="faq">
    <h2 class="abs faq-title">Häufig Gestellte Fragen Und Antworten</h2>
    <svg class="abs bubble" style="left:-230px" width="432" height="122" viewBox="0 0 432 122"><path d="M0 38 Q0 36 30 34 L400 0 Q432 0 432 30 L432 90 Q432 122 400 122 L30 122 Q0 122 0 90Z" fill="#4e8f6b"/></svg>
    <div class="abs bubble-text" style="left:0;top:2386px;width:200px;overflow:hidden;white-space:nowrap">nis iste natus error sit<br>loremque laudantium, to<br>nis iste natus error sit<br>loremque laudantium, to</div>
    <div class="abs avatar" style="left:124px;top:2303px" role="img" aria-label="Kundenporträt"></div>

    <svg class="abs bubble" style="left:292px" width="425" height="122" viewBox="0 0 425 122"><path d="M0 38 Q0 36 30 34 L395 0 Q425 0 425 30 L425 90 Q425 122 395 122 L30 122 Q0 122 0 90Z" fill="#4e8f6b"/></svg>
    <div class="abs bubble-text" style="left:338px;top:2386px;width:360px">Sed ut perspiciatis unde omnis iste natus error sit voluptatem accusantium doloremque laudantium, to Sed ut perspiciatis unde omnis iste natus error sit voluptatem accusantium doloremque laudantium, to</div>
    <div class="abs avatar" style="left:640px;top:2303px" role="img" aria-label="Kundenporträt"></div>

    <svg class="abs bubble" style="left:807px" width="425" height="122" viewBox="0 0 425 122"><path d="M0 38 Q0 36 30 34 L395 0 Q425 0 425 30 L425 90 Q425 122 395 122 L30 122 Q0 122 0 90Z" fill="#4e8f6b"/></svg>
    <div class="abs bubble-text" style="left:853px;top:2386px;width:345px">Sed ut perspiciatis unde omnis iste natus error sit voluptatem accusantium doloremque laudantium, to Sed ut perspiciatis unde omnis iste natus error sit voluptatem accusantium doloremque laudantium, to</div>
    <div class="abs avatar" style="left:1154px;top:2303px" role="img" aria-label="Kundenporträt"></div>

    <span class="abs dot" style="left:488px;background:#1b1b1b"></span>
    <span class="abs dot" style="left:569px"></span>
    <span class="abs dot" style="left:650px"></span>
  </section>

  <footer>
    <div class="abs foot-band"></div>
    <div class="abs foot-col" style="left:35px"><div class="lbl">Postanschrift</div><div>Altmühl Agrarhandel GbR</div><div>Lindenstraße 4</div><div>92399 Grünbach</div></div>
    <div class="abs foot-col" style="left:244px"><div class="lbl">Lieferanschrift</div><div>Altmühl Agrarhandel GbR</div><div>Mühlweg 7</div><div>92399 Grünbach</div></div>
    <div class="abs foot-col" style="left:443px">
      <div class="contact-row"><svg class="ic" viewBox="0 0 14 14"><circle cx="7" cy="7" r="7" fill="#f8ab26"/><path d="M4 4l2 0 1 2-1 1a5 5 0 002 2l1-1 2 1 0 2c-4 0-8-4-7-7z" fill="#fff"/></svg>09100 55 01 20</div>
      <div class="contact-row"><svg class="ic" viewBox="0 0 14 14"><rect x="3" y="1" width="8" height="12" rx="2" fill="#f8ab26"/><rect x="5" y="3" width="4" height="6" fill="#fff"/></svg>0170 000 41 87</div>
      <div class="contact-row"><svg class="ic" viewBox="0 0 14 14"><rect x="0" y="2" width="14" height="10" rx="1" fill="#f8ab26"/><path d="M1 3l6 5 6-5" fill="none" stroke="#fff" stroke-width="1.3"/></svg>Info@Altmuehl-Agrar.De</div>
      <div class="contact-row"><svg class="ic" viewBox="0 0 14 14"><circle cx="7" cy="7" r="6" fill="none" stroke="#f8ab26" stroke-width="1.6"/><path d="M1 7h12M7 1c-3 3-3 9 0 12M7 1c3 3 3 9 0 12" fill="none" stroke="#f8ab26" stroke-width="1.1"/></svg>Www.Altmuehl-Agrar.De</div>
    </div>
    <div class="abs foot-col" style="left:714px"><div>Bankverbindung: Landbank Talheim</div><div>IBAN: DE00 1234 5678 0000 1122 33</div><div>BIC: LANDDEX1TLH</div><div>USt-IdNr.: DE000111222</div></div>
    <div class="abs mini-a" role="img" aria-label="HUPA Prüfsiegel"></div>
    <div class="abs mini-b" role="img" aria-label="BT Qualitätssiegel"></div>
    <p class="abs terms">Es Gelten Die Allgemeinen Lieferungs- Und Zahlungsbedingungen. Die Ware Bleibt Bis Zur Vollständigen Bezahlung<br>Unser Eigentum, Auch Bei Veräußerung, Verfütterung Oder Einer Weiteren Verwendung (Erweiterter Verlängerter Eigentumsvorbehalt).<br>Bei Verspäteter Zahlung Werden Übliche Verzugszinsen Berechnet. Gerichtsstand Ist Talheim I. D. Op</p>
    <div class="abs foot-bottom">Copyright 2023 All Right Reserved</div>
  </footer>

</div>
</body>
</html>
```